Corvane Holdings , new business card design

investment firm with corporate clients . need double sided business card , vertical and horizontal options ,logo must be clear. prefer pantone colors only and sharp design. website also www.corvane.ae

Khalid Bin Tarrafi
Managing Director
Tel. +971 4 387 2940
Mobile +971 50 518 2403
khalid@corvane.ae
Q-Span Plaza, officw 18-B07, Warqa Gardens, Dubai

Contact Information for Business Card

Khalid Bin Tarrafi
Managing Director

Font styles to use
Serif

Colors

Designer to choose colors to be used in the design.

```html
<!DOCTYPE html>
<html lang="en">
<head>
<meta charset="UTF-8">
<title>Corvane Holdings – Business Card</title>
<link rel="stylesheet" href="https://fonts.googleapis.com/css2?family=Lato:wght@400;700&display=swap">
<style>
  :root {
    --backdrop: #e9eaec;
    --card-dark: #0a0d14;
    --card-light: #ffffff;
    --navy: #1d2f6a;
    --steel: #4a78a3;
    --rule: #3d6a9e;
    --ink: #1f2430;
    --white: #ffffff;
  }
  * { box-sizing: border-box; margin: 0; padding: 0; }
  html, body {
    width: 1200px; height: 960px; overflow: hidden;
    background: var(--backdrop);
    font-family: "Lato", sans-serif;
  }
  .canvas {
    width: 1200px; height: 960px;
    display: flex; flex-direction: column; align-items: center; justify-content: center;
    gap: 44px;
  }
  .card {
    width: 700px; height: 400px;
    position: relative;
    box-shadow: 0 6px 18px rgba(0,0,0,.12);
  }
  /* Back side */
  .card--back {
    background: var(--card-dark);
    display: flex; flex-direction: column; align-items: center; justify-content: center;
    gap: 34px;
  }
  .wordmark {
    font-weight: 400;
    text-transform: uppercase;
    letter-spacing: .28em;
    white-space: nowrap;
  }
  .card--back .wordmark { color: var(--white); font-size: 42px; }
  .card--back .website {
    color: var(--white); font-size: 22px; letter-spacing: .22em;
  }
  /* Front side */
  .card--front {
    background: var(--card-light);
    display: grid;
    grid-template-columns: 306px 1fr;
  }
  .brand-panel {
    display: flex; align-items: center; justify-content: center;
    border-right: 2px solid var(--rule);
  }
  .brand-panel .wordmark { color: var(--navy); font-size: 22px; letter-spacing: .2em; }
  .details { display: flex; flex-direction: column; padding-top: 26px; }
  .details__block {
    border-bottom: 2px solid var(--rule);
    padding: 10px 0 10px 22px;
    color: var(--ink);
    font-size: 15.5px;
    line-height: 1.45;
  }
  .details__block:last-child { border-bottom: none; }
  .person__name { font-weight: 700; color: var(--navy); font-size: 17px; letter-spacing: .02em; }
  .person__title { color: var(--navy); font-size: 16px; letter-spacing: .04em; }
  .contact-line { display: flex; align-items: center; gap: 8px; }
  .contact-line svg { width: 14px; height: 14px; flex: none; fill: var(--navy); }
  .address { display: flex; gap: 10px; }
  .address svg { width: 16px; height: 20px; flex: none; fill: var(--navy); margin-top: 2px; }
</style>
</head>
<body>
<main class="canvas">
  <section class="card card--back" aria-label="Card back">
    <p class="wordmark">Corvane Holdings</p>
    <p class="website">www.corvane.ae</p>
  </section>

  <section class="card card--front" aria-label="Card front">
    <div class="brand-panel">
      <p class="wordmark">Corvane Holdings</p>
    </div>
    <div class="details">
      <div class="details__block person">
        <p class="person__name">KHALID BIN TARRAFI</p>
        <p class="person__title">MANAGING DIRECTOR</p>
      </div>
      <div class="details__block">
        <p class="contact-line">
          <svg viewBox="0 0 24 24" aria-hidden="true"><path d="M6.6 10.8a15.1 15.1 0 0 0 6.6 6.6l2.2-2.2a1 1 0 0 1 1-.25 11.4 11.4 0 0 0 3.6.57 1 1 0 0 1 1 1V20a1 1 0 0 1-1 1A17 17 0 0 1 3 4a1 1 0 0 1 1-1h3.5a1 1 0 0 1 1 1c0 1.25.2 2.45.57 3.57a1 1 0 0 1-.25 1z"/></svg>
          +971 4 387 2940
        </p>
        <p class="contact-line">
          <svg viewBox="0 0 24 24" aria-hidden="true"><path d="M8 1h8a2 2 0 0 1 2 2v18a2 2 0 0 1-2 2H8a2 2 0 0 1-2-2V3a2 2 0 0 1 2-2zm0 3v14h8V4zm4 15.5a1.2 1.2 0 1 0 0 2.4 1.2 1.2 0 0 0 0-2.4z"/></svg>
          +971 50 518 2403
        </p>
      </div>
      <div class="details__block">
        <p class="contact-line">
          <svg viewBox="0 0 24 24" aria-hidden="true"><path d="M2 5h20v14H2zm2 2v.5l8 5 8-5V7zm0 2.8V17h16V9.8l-8 5z"/></svg>
          khalid@corvane.ae
        </p>
        <p class="contact-line">
          <svg viewBox="0 0 24 24" aria-hidden="true"><path d="M12 2a10 10 0 1 0 0 20 10 10 0 0 0 0-20zm6.9 6h-2.9a15 15 0 0 0-1.4-3.6A8 8 0 0 1 18.9 8zM12 4a13 13 0 0 1 1.9 4h-3.8A13 13 0 0 1 12 4zM4.3 14a8 8 0 0 1 0-4h3.4a16 16 0 0 0 0 4zm.8 2h2.9a15 15 0 0 0 1.4 3.6A8 8 0 0 1 5.1 16zM8 8H5.1a8 8 0 0 1 4.3-3.6A15 15 0 0 0 8 8zm4 12a13 13 0 0 1-1.9-4h3.8A13 13 0 0 1 12 20zm2.3-6H9.7a14 14 0 0 1 0-4h4.6a14 14 0 0 1 0 4zm.3 5.6A15 15 0 0 0 16 16h2.9a8 8 0 0 1-4.3 3.6zM16.3 14a16 16 0 0 0 0-4h3.4a8 8 0 0 1 0 4z"/></svg>
          www.corvane.ae
        </p>
      </div>
      <div class="details__block address">
        <svg viewBox="0 0 24 30" aria-hidden="true"><path d="M12 0a11 11 0 0 0-11 11c0 8 11 19 11 19s11-11 11-19A11 11 0 0 0 12 0zm0 15.5a4.5 4.5 0 1 1 0-9 4.5 4.5 0 0 1 0 9z"/></svg>
        <p>Q-Span Plaza, officw 18-B07<br>Warqa Gardens, Dubai</p>
      </div>
    </div>
  </section>
</main>
</body>
</html>
```